Local Flower Farm Needs Business Card Design

I need business cards designed for a flower farm based in Eudora, Kansas.
Business Info:
We are a local cut flower farm located in Eudora, Kansas, founded by Corinne Haldwick. What started as a passion for agriculture and search for more joy in daily life has blossomed into a small business dedicated to providing the community with beautiful, fresh, and sustainable flowers. We specialize in local, seasonal blooms, ensuring that every petal reflects the care and dedication we pour into our craft. Our mission is to deliver the highest quality flowers directly to our customers through local farmers markets and to florists who share our commitment to sustainability. Join us in celebrating the beauty of nature, one bloom at a time!
Contact Details:
Corinne Haldwick
Owner
Phone 913-555-0147
Facebook: Rosalind Thorpe Gardens
Instagram: @RosalindThorpeGardens
Website: RosalindThorpeGardens.example
Target Market(s)
Wholesale to Florists and Direct to Consumer via Farmers Market
Industry/Entity Type
Florist, Farm
Contact Information for Business Card
Name, Contact Info, Logo
Look and feel
Each slider illustrates characteristics of the customer's brand and the style your logo design should communicate.

```html
<!DOCTYPE html>
<html lang="en">
<head>
<meta charset="utf-8">
<title>Rosalind Thorpe Gardens – Business Card</title>
<link rel="stylesheet" href="https://fonts.googleapis.com/css2?family=Montserrat:wght@400;500;700&display=swap">
<style>
  :root {
    --backdrop: #6e5a46;
    --card-white: #ffffff;
    --ink-teal: #10292e;
    --ink-body: #1c1c1c;
    --faint-grey: #e4e4e4;
    --back-teal: #0b2a30;
    --pattern-light: #4fc6e6;
    --pattern-dark: #0d2e35;
  }
  * { margin: 0; padding: 0; box-sizing: border-box; }
  html, body { width: 900px; height: 1200px; overflow: hidden; }
  body {
    background: var(--backdrop);
    font-family: "Montserrat", Arial, sans-serif;
    position: relative;
  }
  .card {
    position: absolute;
    left: 80px;
    width: 742px;
    height: 440px;
    border-radius: 22px;
    overflow: hidden;
  }
  .card-front { top: 131px; background: var(--card-white); }
  .card-back  { top: 638px; background: var(--back-teal); }

  .brand-seal {
    position: absolute;
    left: 34px; top: 44px;
    width: 226px; height: 226px;
    border: 2px solid var(--ink-teal);
    border-radius: 50%;
    display: flex; align-items: center; justify-content: center;
    text-align: center;
  }
  .brand-seal .brand-name {
    color: var(--ink-teal);
    font-weight: 700;
    font-size: 22px;
    line-height: 1.25;
    text-transform: uppercase;
    letter-spacing: 1px;
  }
  .holder {
    position: absolute;
    right: 50px; top: 44px;
    text-align: right;
  }
  .holder-name {
    font-weight: 700;
    font-size: 27px;
    color: var(--ink-teal);
    letter-spacing: 0.2px;
  }
  .holder-role {
    font-size: 16px;
    color: var(--ink-body);
    margin-top: 2px;
  }
  .contact-list {
    position: absolute;
    left: 38px; top: 307px;
    list-style: none;
  }
  .contact-list li {
    display: flex; align-items: center;
    height: 25.5px;
    font-size: 16px;
    color: var(--ink-body);
  }
  .contact-list .icon {
    width: 14px; height: 14px;
    margin-right: 10px;
    flex: none;
  }
  .dot-icon {
    width: 13px; height: 13px;
    border-radius: 50%;
    background: var(--ink-body);
    margin-right: 11px;
    flex: none;
  }
  .faint-mark {
    position: absolute;
    left: 480px; top: 190px;
    width: 220px; height: 235px;
    display: flex; align-items: center; justify-content: center;
    text-align: center;
    color: var(--faint-grey);
    font-weight: 700;
    font-size: 38px;
    line-height: 1.1;
    text-transform: uppercase;
  }

  .back-pattern {
    position: absolute; inset: 0;
    background: linear-gradient(120deg, var(--pattern-light) 0%, #2f7f94 22%, #15444e 45%, var(--pattern-dark) 65%, var(--back-teal) 100%);
    opacity: 0.85;
  }
  .back-brand {
    position: absolute;
    left: 480px; top: 272px;
    width: 150px;
    text-align: center;
    color: #ffffff;
    font-weight: 700;
    font-size: 15px;
    line-height: 1.25;
    text-transform: uppercase;
    letter-spacing: 0.5px;
  }
</style>
</head>
<body>
  <section class="card card-front">
    <div class="brand-seal">
      <p class="brand-name">Rosalind<br>Thorpe<br>Gardens</p>
    </div>

    <div class="holder">
      <h1 class="holder-name">Corinne Haldwick</h1>
      <p class="holder-role">Owner</p>
    </div>

    <ul class="contact-list">
      <li>
        <svg class="icon" viewBox="0 0 24 24" aria-hidden="true">
          <path fill="#1c1c1c" d="M6.6 10.8a15.1 15.1 0 0 0 6.6 6.6l2.2-2.2a1 1 0 0 1 1-.25 11.4 11.4 0 0 0 3.6.57 1 1 0 0 1 1 1V20a1 1 0 0 1-1 1A17 17 0 0 1 3 4a1 1 0 0 1 1-1h3.5a1 1 0 0 1 1 1c0 1.25.2 2.45.57 3.57a1 1 0 0 1-.25 1z"/>
        </svg>
        913-555-0147
      </li>
      <li><span class="dot-icon"></span>Rosalind Thorpe Gardens</li>
      <li><span class="dot-icon"></span>@RosalindThorpeGardens</li>
      <li>
        <svg class="icon" viewBox="0 0 24 24" aria-hidden="true">
          <circle cx="12" cy="12" r="10" fill="none" stroke="#1c1c1c" stroke-width="2.4"/>
          <ellipse cx="12" cy="12" rx="4" ry="10" fill="none" stroke="#1c1c1c" stroke-width="2"/>
          <line x1="2" y1="12" x2="22" y2="12" stroke="#1c1c1c" stroke-width="2"/>
        </svg>
        www.RosalindThorpeGardens.example
      </li>
    </ul>

    <div class="faint-mark">Rosalind<br>Thorpe<br>Gardens</div>
  </section>

  <section class="card card-back">
    <div class="back-pattern" role="img" aria-label="Repeating brand monogram pattern fading from light blue to dark teal"></div>
    <p class="back-brand">Rosalind Thorpe Gardens</p>
  </section>
</body>
</html>
```